Business Card for Multi-Brand Sportswear Company

We are looking for a business card which represents our company and the multiple brands within it.

The company: Fen Athletics (LTD)
The brands: Fen, TavaPuni, ElmStretch, Grit and Rain

Employees using these cards would be representing Fen Athletics, rather than any of the individual brands. You will see a current design within the uploaded files, to give some inspiration. The actual text of the brands is not necessary, but the logos should be on there is some format.

Our creative minds on this are stretched, so we are looking for someone to make this their own, and show us what a good business card should look like.

We may like to get these printed with spot gloss, so keep that in mind with your designs.

www.fenathletics.co.uk

Industry/Entity Type

Business

Contact Information for Business Card

Leo Pemberton-Hale
Operations Manager
(+44) 1632 960 418
Leo@fenathletics.co.uk
www.fenathletics.co.uk

Font styles to use
Sans Serif
Other font styles liked:
• Eurostile

Colors
ffffff

Requirements
Nice to have
• Dark (black) background

```html
<!DOCTYPE html>
<html lang="en">
<head>
<meta charset="utf-8">
<title>Fen Athletics – Business Card</title>
<link href="https://fonts.googleapis.com/css2?family=Exo+2:wght@400;600;800&display=swap" rel="stylesheet">
<style>
  :root {
    --stage: #2b2b2b;
    --card: #0b0b0b;
    --card-top: #161616;
    --white: #ffffff;
    --silver: #c9c9c9;
    --red: #e3202a;
    --muted: #8a8a8a;
    --badge: #5a4a66;
  }
  * { margin: 0; padding: 0; box-sizing: border-box; }
  html, body { width: 1200px; height: 900px; overflow: hidden; }
  body {
    background: var(--stage);
    font-family: "Exo 2", Arial, sans-serif;
    color: var(--white);
    position: relative;
  }
  .card {
    position: absolute;
    left: 285px;
    width: 630px;
    height: 360px;
    background: var(--card);
    overflow: hidden;
    box-shadow: 0 10px 30px rgba(0,0,0,.45);
  }
  .card-front { top: 55px; }
  .card-back { top: 485px; }
  .card-curve { position: absolute; inset: 0; width: 100%; height: 100%; }

  .brand-name {
    position: absolute;
    font-weight: 800;
    color: var(--silver);
    letter-spacing: 2px;
    text-transform: uppercase;
    white-space: nowrap;
  }
  .card-front .brand-name { left: 120px; top: 95px; font-size: 46px; }
  .card-back .brand-name { left: 250px; top: 70px; font-size: 46px; }

  .brand-badges {
    position: absolute;
    left: 0; right: 0; top: 238px;
    display: flex; justify-content: center; gap: 18px;
  }
  .brand-badge { width: 34px; height: 26px; }
  .brand-badge--square { background: var(--badge); border-radius: 3px; width: 42px; }
  .brand-badge--outline { border: 2px solid var(--red); border-radius: 4px; }
  .brand-badge--circle { border: 2px solid var(--red); border-radius: 50%; width: 28px; height: 28px; }

  .front-website {
    position: absolute; left: 0; right: 0; top: 282px;
    text-align: center; font-weight: 800; font-size: 19px;
  }
  .accent { color: var(--red); }

  .person {
    position: absolute; left: 118px; top: 258px;
  }
  .person-name { font-weight: 800; font-size: 19px; }
  .person-role { color: var(--red); font-size: 16px; margin-top: 2px; }

  .divider {
    position: absolute; left: 345px; top: 198px;
    width: 1px; height: 62px; background: var(--muted);
  }
  .contact-list {
    position: absolute; left: 362px; top: 194px;
    list-style: none; font-size: 15px; line-height: 22px;
  }
  .contact-item { display: flex; align-items: center; gap: 7px; white-space: nowrap; }
  .contact-icon { width: 13px; height: 13px; flex: none; }

  .address {
    position: absolute; left: 260px; top: 318px;
    font-size: 15px;
  }
  .rule {
    position: absolute; height: 1px; background: var(--red);
  }
  .rule--bottom { left: 0; top: 345px; width: 120px; }
  .rule--top { right: 0; top: 185px; width: 120px; }
</style>
</head>
<body>

<section class="card card-front" aria-label="Card front">
  <svg class="card-curve" viewBox="0 0 630 360" preserveAspectRatio="none">
    <path d="M0 0 H630 V20 Q360 330 0 205 Z" fill="var(--card-top)"/>
    <path d="M0 205 Q360 330 630 20" fill="none" stroke="var(--red)" stroke-width="4"/>
  </svg>
  <div class="brand-name">Fen Athletics</div>
  <div class="brand-badges">
    <span class="brand-badge brand-badge--square" role="img" aria-label="TavaPuni brand mark"></span>
    <span class="brand-badge brand-badge--outline" role="img" aria-label="Grit and Rain brand mark"></span>
    <span class="brand-badge brand-badge--circle" role="img" aria-label="ElmStretch brand mark"></span>
  </div>
  <p class="front-website">www.<span class="accent">fenathletics</span>.co.uk</p>
</section>

<section class="card card-back" aria-label="Card back">
  <svg class="card-curve" viewBox="0 0 630 360" preserveAspectRatio="none">
    <path d="M0 0 H630 V30 Q330 250 0 200 Z" fill="var(--card-top)"/>
    <path d="M0 200 Q330 250 630 30" fill="none" stroke="var(--white)" stroke-width="5"/>
  </svg>
  <div class="brand-name">Fen</div>

  <div class="rule rule--top"></div>
  <div class="divider"></div>
  <ul class="contact-list">
    <li class="contact-item">
      <svg class="contact-icon" viewBox="0 0 14 14"><circle cx="7" cy="7" r="7" fill="var(--red)"/><path d="M4.5 3.5l1.5 1.5-.8 1a5 5 0 0 0 2.8 2.8l1-.8 1.5 1.5-1 1.2A6 6 0 0 1 3.3 4.5z" fill="var(--white)"/></svg>
      <span>(+44) 1632 960 418</span>
    </li>
    <li class="contact-item">
      <svg class="contact-icon" viewBox="0 0 14 14"><circle cx="7" cy="7" r="7" fill="var(--red)"/><rect x="3.5" y="4.5" width="7" height="5" fill="none" stroke="var(--white)" stroke-width="1"/><path d="M3.5 4.5L7 7.3l3.5-2.8" fill="none" stroke="var(--white)" stroke-width="1"/></svg>
      <span>Leo@fenathletics.co.uk</span>
    </li>
    <li class="contact-item">
      <svg class="contact-icon" viewBox="0 0 14 14"><circle cx="7" cy="7" r="7" fill="var(--red)"/><circle cx="7" cy="7" r="3.6" fill="none" stroke="var(--white)" stroke-width="1"/><path d="M3.4 7h7.2M7 3.4v7.2" stroke="var(--white)" stroke-width=".8"/></svg>
      <span>www.<span class="accent">fenathletics</span>.co.uk</span>
    </li>
  </ul>

  <div class="person">
    <p class="person-name">Leo Pemberton-Hale</p>
    <p class="person-role">Operations Manager</p>
  </div>
  <p class="address">Lower Green, Ashby Fen, Norwich, NR9 4QT</p>
  <div class="rule rule--bottom"></div>
</section>

</body>
</html>
```